Business card design/logo/website name

I am a business coach. My business name is KDP (Kessel Dunmore & Partners, Inc.) I want to use this card just for coaching. I do two kinds: Personal Image coach and Executive business coach
1. I work with people to become a polished global professional.
"Become a confident, savvy professional building relationships tactfully and appropriately while clearly representing your own company’s message and image.
Learn the nuances… Master the skills… Use the business etiquette techniques and protocols that allow you to seamlessly and confidently conduct business in a global business environment.
Have the comfort of knowing what to expect, what to do and how to easily build long and short-term relationships that give you the winning edge and increased company profits."
2. Leadership Coaching
For increasing the team’s productivity by building stronger relationships. Build strong compelling vision and write and share their Personal Leadership Philosophy, a roadmap that is concise and commanding and gives the team a clear vision of the leader's expectations.
Updates

KDP should be the logo. (Downplay the Kessel Dunmore and Partners, Inc.)

Want:
Executive Coach
Consultant

Reason: I am traveling and connections are often broken.

Target Market(s)

Executives, business people

Industry/Entity Type

Building

Font styles to use
Sans Serif
Script

Colors
0255a3
3176b5
85acd3
ec2027

Requirements
Must have
• KDP as the logo,(no preference on how you treat KDP) with Kessel Dunmore & Partners. Inc. downplayed.
On the card:
Rosalind Dunmore CEO
Executive Coach
Consultant
KRC 4(c)
Coaching - Training - Strategic Planning

```html
<!DOCTYPE html>
<html lang="en">
<head>
<meta charset="utf-8">
<title>Kessel Dunmore &amp; Partners, Inc. – Business Card</title>
<link rel="stylesheet" href="https://fonts.googleapis.com/css2?family=Arimo:wght@400;700&display=swap">
<style>
  :root {
    --stage: #e9ecef;
    --card-light: #5a9bd6;
    --card-mid: #3f7fbf;
    --card-dark: #163f6c;
    --brand-blue: #0255a3;
    --band-blue: #3176b5;
    --ink-blue: #1b4e8e;
    --accent-orange: #f07a22;
    --pattern-tint: rgba(133, 172, 211, 0.35);
  }
  * { margin: 0; padding: 0; box-sizing: border-box; }
  html, body {
    width: 1200px; height: 1000px; overflow: hidden;
    background: var(--stage);
    font-family: "Arimo", Arial, sans-serif;
  }
  .canvas { position: relative; width: 1200px; height: 1000px; }
  .card {
    position: absolute; left: 290px; width: 620px; height: 354px;
    overflow: hidden;
    box-shadow: 0 10px 26px rgba(0,0,0,0.25);
  }
  .card--front {
    top: 100px;
    background: linear-gradient(100deg, var(--card-light) 0%, var(--card-mid) 40%, var(--card-dark) 100%);
  }
  .card--back {
    top: 546px;
    background: linear-gradient(100deg, var(--card-light) 0%, #4a8ccc 30%, #2a5d93 55%, var(--card-dark) 80%);
  }
  .card__shapes { position: absolute; inset: 0; }
  .pattern-area {
    position: absolute; left: 140px; top: 40px; width: 230px; height: 230px;
    border-radius: 50%;
    background: radial-gradient(circle, var(--pattern-tint) 0%, rgba(133,172,211,0.15) 55%, rgba(133,172,211,0) 72%);
  }
  .brand { position: absolute; left: 30px; top: 18px; }
  .brand__name {
    font-weight: 700; font-size: 66px; line-height: 1; letter-spacing: 2px;
    color: var(--brand-blue);
  }
  .brand__legal {
    font-weight: 700; font-size: 10.5px; text-transform: uppercase;
    color: var(--accent-orange); margin-top: 2px; letter-spacing: 0.2px;
  }
  .details { position: absolute; left: 30px; top: 112px; color: var(--ink-blue); }
  .details__name { font-weight: 700; font-size: 22px; }
  .details__role { font-weight: 700; font-size: 16px; margin-top: 2px; }
  .details__services { font-size: 16px; margin-top: 10px; }
  .contact { list-style: none; margin-top: 10px; font-size: 13.5px; line-height: 1.3; }
  .contact li { display: flex; align-items: flex-start; gap: 7px; margin-bottom: 2px; }
  .contact svg { width: 11px; height: 11px; margin-top: 3px; flex: none; fill: var(--ink-blue); }
  .back-brand {
    position: absolute; left: 0; right: 0; top: 92px; text-align: center;
  }
  .back-brand .brand__name { font-size: 118px; letter-spacing: 4px; }
  .back-brand .brand__legal { font-size: 15px; margin-top: 4px; }
</style>
</head>
<body>
<main class="canvas">
  <section class="card card--front" aria-label="Card front">
    <div class="pattern-area" role="img" aria-label="Faint circular line ornament"></div>
    <svg class="card__shapes" viewBox="0 0 620 354" preserveAspectRatio="none" aria-hidden="true">
      <path d="M480,0 Q515,140 620,205 L620,0 Z" fill="var(--brand-blue)"/>
      <path d="M525,0 Q560,105 620,150 L620,0 Z" fill="var(--accent-orange)"/>
      <path d="M285,354 Q400,205 620,178 L620,354 Z" fill="var(--band-blue)"/>
      <path d="M318,354 Q420,228 620,214 L620,354 Z" fill="var(--accent-orange)"/>
    </svg>
    <div class="brand">
      <div class="brand__name">KDP</div>
      <div class="brand__legal">Kessel Dunmore &amp; Partners, Inc</div>
    </div>
    <div class="details">
      <p class="details__name">Rosalind L. Dunmore, CEO</p>
      <p class="details__role">Global Executive Coach</p>
      <p class="details__services">Training, Coaching, Diversity, Protocol</p>
      <ul class="contact">
        <li><svg viewBox="0 0 12 12"><path d="M6 1 L11 6 H9.5 V11 H7 V8 H5 V11 H2.5 V6 H1 Z"/></svg><span>4420 Harbor Crest Dr, Tampa,<br>FL 33609, United States</span></li>
        <li><svg viewBox="0 0 12 12"><path d="M1 4 Q6 0 11 4 L9.5 5.5 L8 4.5 L8 3.5 Q6 3 4 3.5 L4 4.5 L2.5 5.5 Z M3 6 H9 L10 11 H2 Z"/></svg><span>(555) 314-0282</span></li>
        <li><svg viewBox="0 0 12 12"><path d="M1 2.5 H11 V9.5 H1 Z M1.5 3 L6 6.5 L10.5 3" stroke="#5a9bd6" stroke-width="0.8"/></svg><span>rdunmore@kesseldunmore.com</span></li>
        <li><svg viewBox="0 0 12 12"><path d="M4 8 L8 4" stroke="#1b4e8e" stroke-width="1.4"/><rect x="1" y="6" width="5" height="3" rx="1.5" transform="rotate(-45 3.5 7.5)" fill="none" stroke="#1b4e8e" stroke-width="1.2"/><rect x="6" y="3" width="5" height="3" rx="1.5" transform="rotate(-45 8.5 4.5)" fill="none" stroke="#1b4e8e" stroke-width="1.2"/></svg><span>kesseldunmore.com</span></li>
      </ul>
    </div>
  </section>

  <section class="card card--back" aria-label="Card back">
    <div class="back-brand">
      <div class="brand__name">KDP</div>
      <div class="brand__legal">Kessel Dunmore &amp; Partners, Inc</div>
    </div>
  </section>
</main>
</body>
</html>
```